Thornvale Group needs a business card design

We need a new business card design using the logo recently selected in a logo competition on Pixel Bazaar. Our business is a consultancy specializing in aviation and energy and the winning business card design will promote an image of precision and professionalism with creativity.

Please use the logo with the name on the front of the card and use a complementary font. Make the back white with either the light grey or dark grey logo.

Target Market(s)

Senior finance and legal leaders at aviation and energy companies

Industry/Entity Type

Management Consulting

Contact Information for Business Card

Peter Castrell
President
Thornvale Group

www.thornvalegroup.example

(555) 204-6391
pc@thornvalegroup.example

Requirements
Must have
• Professional font that goes well with the logo font

```html
<!DOCTYPE html>
<html lang="en">
<head>
<meta charset="utf-8">
<title>Thornvale Group — Business Card</title>
<link href="https://fonts.googleapis.com/css2?family=Open+Sans:wght@400;600;700&display=swap" rel="stylesheet">
<style>
  :root {
    --navy: #173a64;
    --blue: #1f6a9a;
    --steel: #b7c2d6;
    --ink-grey: #6f7276;
    --line-grey: #9a9da1;
    --logo-grey: #5f6368;
    --paper: #ffffff;
    --backdrop: #e9eaec;
  }
  * { margin: 0; padding: 0; box-sizing: border-box; }
  html, body { width: 1200px; height: 913px; overflow: hidden; }
  body {
    background: var(--backdrop);
    font-family: "Open Sans", Arial, sans-serif;
    position: relative;
  }
  .card {
    position: absolute;
    top: 308px;
    width: 520px;
    height: 297px;
    border-radius: 18px;
    overflow: hidden;
    background: var(--paper);
    box-shadow: 0 6px 18px rgba(0,0,0,0.18);
  }
  .card--front { left: 50px; }
  .card--back { left: 630px; }
  .card__art { position: absolute; inset: 0; }

  .brand {
    position: absolute;
    display: flex;
    align-items: center;
    gap: 10px;
    font-weight: 400;
    letter-spacing: 2px;
    text-transform: uppercase;
    white-space: nowrap;
  }
  .brand__mark { display: block; width: 14px; height: 14px; }
  .card--front .brand { left: 34px; top: 96px; font-size: 22px; color: var(--navy); }
  .card--front .brand__mark { background: var(--navy); }
  .card--back .brand {
    left: 0; right: 0; top: 128px; justify-content: center;
    font-size: 32px; color: var(--logo-grey); letter-spacing: 3px;
  }
  .card--back .brand__mark { background: var(--logo-grey); width: 18px; height: 18px; }

  .person {
    position: absolute;
    right: 48px;
    top: 44px;
    text-align: right;
  }
  .person__name { font-size: 20px; font-weight: 700; color: var(--navy); line-height: 1.1; }
  .person__title {
    font-size: 11px; color: var(--ink-grey);
    border-top: 1px solid var(--line-grey);
    margin-top: 3px; padding-top: 1px;
  }
  .name-tab {
    position: absolute; right: 0; top: 36px;
    width: 34px; height: 44px; background: var(--blue);
  }
  .contact {
    position: absolute;
    left: 210px;
    top: 218px;
    list-style: none;
    color: var(--paper);
    font-size: 12.5px;
    line-height: 1.45;
  }
</style>
</head>
<body>

<section class="card card--front" aria-label="Card front">
  <svg class="card__art" viewBox="0 0 520 297" aria-hidden="true">
    <line x1="60" y1="245" x2="420" y2="100" stroke="var(--line-grey)" stroke-width="1"/>
    <polygon points="0,262 520,150 520,297 0,297" fill="var(--navy)"/>
    <polygon points="0,268 190,228 165,297 0,297" fill="var(--steel)"/>
    <g transform="translate(28,270)" fill="none" stroke="var(--navy)" stroke-width="1.6">
      <path d="M2 1 l4 0 l1 4 l-2 1.5 q2 4 6 6 l1.5 -2 l4 1 l0 4 q-10 0 -14.5 -14.5z"/>
    </g>
    <g transform="translate(70,271)" fill="none" stroke="var(--navy)" stroke-width="1.6">
      <rect x="0" y="0" width="18" height="13" rx="1"/>
      <path d="M0 0 l9 7 l9 -7"/>
    </g>
    <g transform="translate(120,277)" fill="none" stroke="var(--navy)" stroke-width="1.5">
      <circle cx="0" cy="0" r="8"/>
      <ellipse cx="0" cy="0" rx="3.5" ry="8"/>
      <line x1="-8" y1="0" x2="8" y2="0"/>
    </g>
  </svg>

  <div class="brand"><span class="brand__mark"></span>Thornvale Group</div>

  <div class="name-tab"></div>
  <div class="person">
    <div class="person__name">Peter Castrell</div>
    <div class="person__title">President</div>
  </div>

  <ul class="contact">
    <li>(555) 204-6391</li>
    <li>pc@thornvalegroup.example</li>
    <li>www.thornvalegroup.example</li>
  </ul>
</section>

<section class="card card--back" aria-label="Card back">
  <div class="brand"><span class="brand__mark"></span>Thornvale Group</div>
</section>

</body>
</html>
```